One business card required with 2 company logos and 2 people's details

One business card required.
No preference on design - One side could show the 2 different business logos for the companies we own. The reverse could have the details shown below.
Another option could be one business one side and one business on the reverse. Happy to receive designs.

Dora Pellham
07700 913 286
Rowena Tindall
07700 958 137

website: quietmeadowbloom.co.uk
email: info@quietmeadowbloom.co.uk

website: brightharbourevents.co.uk
email: info:brightharbourevents.co.uk

May be nice to have icons instead of the words email/website?

I have included different versions of the logos to help with your design.

Contact Information for Business Card

see project overview

Requirements
Must have
• both company logos, both contact names and contact details

```html
<!DOCTYPE html>
<html lang="en">
<head>
<meta charset="utf-8">
<title>Quiet Meadow Bloom &amp; Bright Harbour Events – Business Card</title>
<link href="https://fonts.googleapis.com/css2?family=Raleway:wght@500;600&display=swap" rel="stylesheet">
<style>
  :root {
    --stage: #e4e4e6;
    --navy-deep: #161c27;
    --navy: #1e2633;
    --slate: #4a525c;
    --paper: #f7f7f8;
    --ink: #2e3452;
    --teal: #6cc3cf;
    --teal-soft: #8fd0d8;
    --white: #ffffff;
    --glow: rgba(70, 140, 170, 0.35);
  }
  * { box-sizing: border-box; margin: 0; padding: 0; }
  html, body {
    width: 1200px; height: 985px; overflow: hidden;
    background: var(--stage);
    font-family: "Raleway", Arial, sans-serif;
  }
  .canvas { position: relative; width: 1200px; height: 985px; }
  .card {
    position: absolute; top: 182px;
    width: 380px; height: 620px;
    overflow: hidden;
    box-shadow: 0 10px 28px rgba(0,0,0,0.18);
  }
  .card--front {
    left: 180px;
    background: linear-gradient(160deg, var(--navy-deep) 40%, var(--navy) 65%, var(--slate) 100%);
  }
  .card--back {
    left: 640px;
    background:
      radial-gradient(ellipse 190px 150px at 50% 40%, var(--glow), transparent 75%),
      linear-gradient(165deg, var(--navy-deep) 35%, var(--navy) 60%, var(--slate) 100%);
  }
  .front-top { position: absolute; inset: 0; width: 380px; height: 620px; }
  .brand-name {
    position: absolute; left: 0; right: 0;
    text-align: center;
    font-weight: 600;
    line-height: 1.15;
  }
  .card--front .brand-name { top: 150px; font-size: 34px; color: var(--ink); }
  .card--back .brand-name { top: 200px; font-size: 30px; color: var(--white); }
  .contacts {
    position: absolute; top: 352px; left: 0; right: 0;
    text-align: center; color: var(--white);
  }
  .person { margin-bottom: 22px; }
  .person__name { font-size: 26px; font-weight: 600; color: var(--teal); }
  .person__phone {
    margin-top: 6px; font-size: 15px; font-weight: 500;
    display: flex; align-items: center; justify-content: center; gap: 12px;
  }
  .icon { width: 15px; height: 15px; fill: var(--teal-soft); }
  .web {
    position: absolute; bottom: 34px; left: 0; right: 0;
    text-align: center; color: var(--white);
    font-size: 14.5px; font-weight: 500; line-height: 1.55;
  }
  .web__icons { display: flex; justify-content: center; gap: 18px; margin-bottom: 6px; }
  .accent-bar {
    position: absolute; left: 0; right: 0; bottom: 0; height: 10px;
    background: var(--teal-soft);
  }
</style>
</head>
<body>
<main class="canvas">

  <section class="card card--front" aria-label="Business card front">
    <svg class="front-top" viewBox="0 0 380 620" aria-hidden="true">
      <path d="M0 0 H380 V250 H299.5 A130 130 0 0 1 80.5 250 H0 Z" fill="var(--paper)"/>
    </svg>
    <p class="brand-name">Quiet Meadow<br>Bloom</p>

    <div class="contacts">
      <div class="person">
        <p class="person__name">Dora Pellham</p>
        <p class="person__phone">
          <svg class="icon" viewBox="0 0 24 24" aria-hidden="true"><path d="M6.6 10.8a15.1 15.1 0 0 0 6.6 6.6l2.2-2.2a1 1 0 0 1 1-.25 11.4 11.4 0 0 0 3.6.57 1 1 0 0 1 1 1V20a1 1 0 0 1-1 1A17 17 0 0 1 3 4a1 1 0 0 1 1-1h3.5a1 1 0 0 1 1 1c0 1.25.2 2.45.57 3.57a1 1 0 0 1-.25 1z"/></svg>
          07700 913 286
        </p>
      </div>
      <div class="person">
        <p class="person__name">Rowena Tindall</p>
        <p class="person__phone">
          <svg class="icon" viewBox="0 0 24 24" aria-hidden="true"><path d="M6.6 10.8a15.1 15.1 0 0 0 6.6 6.6l2.2-2.2a1 1 0 0 1 1-.25 11.4 11.4 0 0 0 3.6.57 1 1 0 0 1 1 1V20a1 1 0 0 1-1 1A17 17 0 0 1 3 4a1 1 0 0 1 1-1h3.5a1 1 0 0 1 1 1c0 1.25.2 2.45.57 3.57a1 1 0 0 1-.25 1z"/></svg>
          07700 958 137
        </p>
      </div>
    </div>

    <div class="web">
      <div class="web__icons">
        <svg class="icon" viewBox="0 0 24 24" aria-label="Email"><path d="M2 5h20v14H2z M3.5 6.5 12 13l8.5-6.5" fill="none" stroke="var(--teal-soft)" stroke-width="2"/></svg>
        <svg class="icon" viewBox="0 0 24 24" aria-label="Website"><g fill="none" stroke="var(--teal-soft)" stroke-width="1.8"><circle cx="12" cy="12" r="9.5"/><ellipse cx="12" cy="12" rx="4.2" ry="9.5"/><path d="M2.5 12h19M4 7h16M4 17h16"/></g></svg>
      </div>
      <p>info@quietmeadowbloom.co.uk</p>
      <p>www.quietmeadowbloom.co.uk</p>
    </div>
    <div class="accent-bar"></div>
  </section>

  <section class="card card--back" aria-label="Business card back">
    <p class="brand-name">Bright Harbour<br>Events</p>

    <div class="web">
      <div class="web__icons">
        <svg class="icon" viewBox="0 0 24 24" aria-label="Email"><path d="M2 5h20v14H2z M3.5 6.5 12 13l8.5-6.5" fill="none" stroke="var(--teal-soft)" stroke-width="2"/></svg>
        <svg class="icon" viewBox="0 0 24 24" aria-label="Website"><g fill="none" stroke="var(--teal-soft)" stroke-width="1.8"><circle cx="12" cy="12" r="9.5"/><ellipse cx="12" cy="12" rx="4.2" ry="9.5"/><path d="M2.5 12h19M4 7h16M4 17h16"/></g></svg>
      </div>
      <p>info:brightharbourevents.co.uk</p>
      <p>www.brightharbourevents.co.uk</p>
    </div>
  </section>

</main>
</body>
</html>
```